Company or website name
- Velmira, LLC
- Velmira, LLC
- Describe your company and organization and target audience
- Velmira, LLC is a research, science and technology based manufacturing company that formulates, develops, manufactures and packages a full complement of personal care products for domestic and international concerns. We private label and contract package personal care products, cosmetics, bath salts and powders and home fragrance products. Velmira is conveniently located in Southern California adjacent to major transportation hubs and international airports. We utilize earth friendly, green manufacturing processes, maximize the use of renewable resource raw materials and minimize the use of non-renewable and petrochemical based raw materials. We provide formulation and product development services with low minimum order quantities and short lead times. Velmira is the intersection between nature, science, beauty and innovation. We are a B-2-B company.
- The design should have the following
- We're looking for an ad design that can be used for both banner and column use online and in print. We manufacture bath and body products such as bath salts, body washes, body powders, bath oils and bubble baths, hair care products such as shampoos, conditioners and styling aids, skin care products such as anti-aging creams, cleansers, masks, toners and serums, color cosmetics such as eyeliners, mascaras, foundations and mineral make-up powders, manicure/pedicure products such as cuticle oils, sugar and salt scrubs and foot soaks/softeners and spa products such as seaweed wraps, cellulite creams, body masks, massage oils and candles. Our strengths are natural and organic product formulation, low minimums, competitive prices, complete research &development services new and innovative ingredients and fast turnaround times. Examples can be found at the following sites: http://www.glintor.com/ http://www.grovewellboard.org/ http://www.tessaloomjournal.com/ http://nerwast.org/images/downloads/bulletins/2009-10-bulletin.pdf http://www.pantrykestrelworks.com/

```html
<!DOCTYPE html>
<html lang="en">
<head>
<meta charset="utf-8">
<title>Velmira Print Ads</title>
<link href="https://fonts.googleapis.com/css2?family=Source+Sans+3:wght@400;600;700&display=swap" rel="stylesheet">
<style>
:root{
  --stage:#000;
  --white:#fff;
  --ink:#3a3a46;
  --grey:#55565c;
  --purple:#6b3f8f;
  --pink:#e8417a;
  --tan:#b38c55;
  --green:#2fb24a;
  --hair-green:#5bb530;
  --teal:#3aa6b6;
  --navy:#2b3590;
  --night:#2a2b3d;
  --forest:#1e9e4c;
  --bullet-blue:#2f3b8f;
  --badge-dark:#3b3b3f;
  --badge-red:#c9302c;
}
*{margin:0;padding:0;box-sizing:border-box}
html,body{width:1200px;height:482px;overflow:hidden;background:var(--stage);font-family:"Source Sans 3",Arial,sans-serif}
.stage{position:relative;width:1200px;height:482px}
.ad{position:absolute;top:75px;width:247px;height:333px;background:var(--white);overflow:hidden}
.ad-1{left:79px}.ad-2{left:344px}.ad-3{left:610px}.ad-4{left:875px}

.hero{position:absolute;left:0;top:0;width:247px;height:197px}
.ad-1 .hero{background:
  linear-gradient(200deg,rgba(190,150,150,.85) 0%,rgba(190,150,150,0) 45%),
  linear-gradient(160deg,#8fa0c8 0%,#3b4f98 40%,#1f2f72 70%,#2c4a8a 100%)}
.ad-2 .hero{background:
  linear-gradient(200deg,rgba(235,245,250,.9) 0%,rgba(235,245,250,0) 40%),
  linear-gradient(160deg,#4a9cc9 0%,#9ad8ef 40%,#2f7fb4 75%,#123f6e 100%)}
.ad-3 .hero{background:
  linear-gradient(180deg,#f1f3f6 0%,#dfe6e2 30%,#a8c38c 50%,#d88a74 75%,#b8412f 100%)}
.ad-4 .hero{background:
  linear-gradient(200deg,rgba(245,248,250,.95) 0%,rgba(245,248,250,0) 45%),
  linear-gradient(160deg,#7fc3d8 0%,#bfe3ee 40%,#4aa8c4 70%,#1d6f8c 100%)}

.brand{position:absolute;top:5px;width:75px;height:29px;background:var(--white);border-radius:2px;display:flex;align-items:center;justify-content:center;gap:3px;font-weight:700;font-size:13px;color:var(--tan)}
.ad-1 .brand,.ad-2 .brand,.ad-3 .brand{left:12px}
.ad-4 .brand{right:12px}
.brand-dot{width:6px;height:6px;border-radius:50%;background:var(--hair-green)}

.headline{position:absolute;left:19px;top:213px;line-height:1;white-space:nowrap}
.headline-lead{font-size:11.5px;font-weight:600;color:var(--ink)}
.headline-main{font-size:15.5px;font-weight:600;margin-top:2px}
.ad-1 .headline-main{color:var(--purple)}
.ad-2 .headline-main{color:var(--green)}
.ad-3 .headline-main{color:var(--pink)}
.ad-4 .headline-main{color:var(--teal)}

.category{position:absolute;left:0;top:253px;width:247px;height:10px}
.category-rule{position:absolute;left:0;right:0;top:4.5px;height:1px}
.category-pill{position:absolute;left:0;top:0;height:10px;width:87px;border-radius:0 5px 5px 0;padding-left:18px;font-size:6.5px;font-weight:700;color:var(--white);line-height:10px;white-space:nowrap}
.ad-1 .category-pill,.ad-1 .category-rule{background:var(--pink)}
.ad-2 .category-pill,.ad-2 .category-rule{background:var(--tan)}
.ad-3 .category-pill,.ad-3 .category-rule{background:var(--hair-green)}
.ad-4 .category-pill,.ad-4 .category-rule{background:var(--navy)}

.products{position:absolute;left:19px;top:267px;font-size:5.8px;color:var(--grey);line-height:7.5px;white-space:nowrap}
.strengths{position:absolute;left:19px;top:292px;list-style:none;font-size:4.8px;font-weight:700;color:var(--bullet-blue);line-height:5.8px;white-space:nowrap}
.strengths li::before{content:"• ";color:var(--pink)}

.badges{position:absolute;left:94px;top:292px;display:flex;flex-direction:column;align-items:center;gap:4px}
.badge-mark{width:17px;height:8px;background:var(--badge-dark);border-radius:1px}
.badge-seal{width:13px;height:9px;background:var(--badge-red);border-radius:50%}

.packshot{position:absolute;left:118px;top:244px;width:124px;height:70px}
.ad-1 .packshot{background:linear-gradient(90deg,rgba(255,255,255,0) 0%,#e6dcef 12%,#9d86c0 40%,#c9a98a 70%,#f3ece4 92%,rgba(255,255,255,0) 100%)}
.ad-2 .packshot{background:linear-gradient(90deg,rgba(255,255,255,0) 0%,#f3e9d8 15%,#dcc196 40%,#c9a46a 65%,#efe2cb 90%,rgba(255,255,255,0) 100%)}
.ad-3 .packshot{background:linear-gradient(90deg,rgba(255,255,255,0) 0%,#f6c9d6 15%,#ee8fb0 35%,#f3b24a 55%,#8fd0df 78%,rgba(255,255,255,0) 100%)}
.ad-4 .packshot{background:linear-gradient(90deg,rgba(255,255,255,0) 0%,#eef2f2 15%,#d8e2e3 40%,#9cb58a 58%,#e4ebec 80%,rgba(255,255,255,0) 100%)}

.footer{position:absolute;left:0;bottom:0;width:247px;height:17px;color:var(--white);font-size:5.2px;text-align:center;line-height:6px;padding-top:2.5px;white-space:nowrap}
.ad-1 .footer{background:var(--purple)}
.ad-2 .footer{background:var(--tan)}
.ad-3 .footer{background:var(--night)}
.ad-4 .footer{background:var(--forest)}

.spec{position:absolute;right:78px;top:432px;text-align:right;color:var(--white);font-family:Arial,Helvetica,sans-serif;font-weight:700;line-height:1}
.spec-title{font-size:13.5px}
.spec-size{font-size:10px;margin-top:3px}
</style>
</head>
<body>
<main class="stage">

<article class="ad ad-1">
  <div class="hero" role="img" aria-label="Gloved hand holding a glass flask with fresh green leaves"></div>
  <div class="brand"><span class="brand-dot"></span>Velmira</div>
  <div class="headline"><p class="headline-lead">Creating Innovative Products by</p><p class="headline-main">Blending Science and Nature</p></div>
  <div class="category"><span class="category-rule"></span><span class="category-pill">Bath &amp; Body Products</span></div>
  <p class="products">Bath Salts &nbsp;|&nbsp; Body Powders &nbsp;|&nbsp; Body Gels<br>Lotions &nbsp;|&nbsp; Baths Oils</p>
  <ul class="strengths"><li>Natural Product Formulation</li><li>Fast Turnaround</li><li>Competitive Pricing</li><li>Low Minimums</li></ul>
  <div class="badges"><span class="badge-mark"></span><span class="badge-seal"></span></div>
  <div class="packshot" role="img" aria-label="Lavender bath salts in a bowl with a bar of soap"></div>
  <footer class="footer">4120 E. Larkspur Avenue, Building 210, Corvena, CA 92817<br>P 555.210.4401 &nbsp;|&nbsp; F 555.210.4402 &nbsp;|&nbsp; E info@velmira.com</footer>
</article>

<article class="ad ad-2">
  <div class="hero" role="img" aria-label="Scientist examining a test tube in a blue-lit laboratory"></div>
  <div class="brand"><span class="brand-dot"></span>Velmira</div>
  <div class="headline"><p class="headline-lead">Creating Innovative Products by</p><p class="headline-main">Blending Science and Nature</p></div>
  <div class="category"><span class="category-rule"></span><span class="category-pill">Skin Care Products</span></div>
  <p class="products">Serums &nbsp;|&nbsp; Creams Toner<br>Anti-aging Products</p>
  <ul class="strengths"><li>Natural Product Formulation</li><li>Fast Turnaround</li><li>Competitive Pricing</li><li>Low Minimums</li></ul>
  <div class="badges"><span class="badge-mark"></span><span class="badge-seal"></span></div>
  <div class="packshot" role="img" aria-label="Gold skin care bottles and cream jars"></div>
  <footer class="footer">4120 E. Larkspur Avenue, Building 210, Corvena, CA 92817<br>P 555.210.4401 &nbsp;|&nbsp; F 555.210.4402 &nbsp;|&nbsp; E info@velmira.com</footer>
</article>

<article class="ad ad-3">
  <div class="hero" role="img" aria-label="Green seedlings growing out of rows of test tubes"></div>
  <div class="brand"><span class="brand-dot"></span>Velmira</div>
  <div class="headline"><p class="headline-lead">Creating Innovative Products by</p><p class="headline-main">Blending Science and Nature</p></div>
  <div class="category"><span class="category-rule"></span><span class="category-pill">Hair Care Products</span></div>
  <p class="products">Shampoos &nbsp;|&nbsp; Conditioners &nbsp;|&nbsp; Pomades<br>Styling Products</p>
  <ul class="strengths"><li>Natural Product Formulation</li><li>Fast Turnaround</li><li>Competitive Pricing</li><li>Low Minimums</li></ul>
  <div class="badges"><span class="badge-mark"></span><span class="badge-seal"></span></div>
  <div class="packshot" role="img" aria-label="Colourful shampoo and conditioner bottles with towels"></div>
  <footer class="footer">4120 E. Larkspur Avenue, Building 210, Corvena, CA 92817<br>P 555.210.4401 &nbsp;|&nbsp; F 555.210.4402 &nbsp;|&nbsp; E info@velmira.com</footer>
</article>

<article class="ad ad-4">
  <div class="hero" role="img" aria-label="Gloved hand using a pipette over blue laboratory glassware"></div>
  <div class="brand"><span class="brand-dot"></span>Velmira</div>
  <div class="headline"><p class="headline-lead">Creating Innovative Products by</p><p class="headline-main">Blending Science and Nature</p></div>
  <div class="category"><span class="category-rule"></span><span class="category-pill">Baby Products</span></div>
  <p class="products">Shampoos &nbsp;|&nbsp; Bubble Bath &nbsp;|&nbsp; Lotions<br>Baby Powders</p>
  <ul class="strengths"><li>Natural Product Formulation</li><li>Fast Turnaround</li><li>Competitive Pricing</li><li>Low Minimums</li></ul>
  <div class="badges"><span class="badge-mark"></span><span class="badge-seal"></span></div>
  <div class="packshot" role="img" aria-label="White baby care bottles and tubes with a leaf"></div>
  <footer class="footer">4120 E. Larkspur Avenue, Building 210, Corvena, CA 92817<br>P 555.210.4401 &nbsp;|&nbsp; F 555.210.4402 &nbsp;|&nbsp; E info@velmira.com</footer>
</article>

<div class="spec"><p class="spec-title">PRINT AD</p><p class="spec-size">Full Page : 8.25" x 11.125</p></div>

</main>
</body>
</html>
```